Business Card Design Project for an English Teacher

I need a business card design for my new job.
I'd like to start teaching English as a freelance.
My students will be children, teenager, and adults, who don't like or hesitate to study English and I would like to open a door to the new world for them.

I'd like to put the information below;
[right side]
1. name
2. mail address
3. mobile number
4. website or facebook page

[back]
1.my message: Feel free at asking me anything about my classes

2.lesson list such as:
price: 3150 yen ~

calsses:
kids class( mum& dad can join) ... 30 minutes / 45 minutes
students (over age 13).... 60minutes / 90 minutes
Adult (over age 19) .... 60 minutes / 90 minutes

3. I'll have both Web Lesson and Face to Face Lesson

4. Free trial lesson

Target Market(s)

My students will be children, teenager, and adults, who don't like or hesitate to study English

Industry/Entity Type

Business

Requirements
Must have
• designed both side

```html
<!DOCTYPE html>
<html lang="en">
<head>
<meta charset="UTF-8">
<title>English Teacher Business Card</title>
<link rel="stylesheet" href="https://fonts.googleapis.com/css2?family=Source+Sans+3:wght@400;600&display=swap">
<style>
  :root {
    --stage: #ececec;
    --card-white: #ffffff;
    --sky: #29a8e0;
    --sky-light: #8fd3f3;
    --accent-blue: #2aa6dd;
    --ink-grey: #6d6e70;
    --rule-grey: #b9b9b9;
    --sun-yellow: #f6ec2a;
    --on-blue: #ffffff;
  }
  * { margin: 0; padding: 0; box-sizing: border-box; }
  html, body {
    width: 1200px; height: 836px; overflow: hidden;
    background: var(--stage);
    font-family: "Source Sans 3", Arial, sans-serif;
  }
  .card {
    position: absolute; left: 345px; width: 510px; height: 290px;
    box-shadow: 0 4px 14px rgba(0,0,0,.18);
  }
  /* Front side */
  .card-front { top: 92px; background: var(--card-white); }
  .identity { position: absolute; left: 100px; top: 124px; line-height: 1.15; }
  .identity-name { color: var(--accent-blue); font-size: 15px; }
  .identity-role { color: var(--ink-grey); font-size: 15px; }
  .divider {
    position: absolute; left: 255px; top: 108px; width: 2px; height: 66px;
    background: var(--rule-grey);
  }
  .contact-list {
    position: absolute; left: 278px; top: 104px; list-style: none;
    color: var(--ink-grey); font-size: 13.5px; line-height: 19px;
  }
  .contact-list li { display: flex; align-items: center; gap: 6px; }
  .contact-list svg { width: 11px; height: 11px; flex: none; }
  .domain { color: var(--accent-blue); }
  /* Back side */
  .card-back {
    top: 442px; color: var(--on-blue);
    background: radial-gradient(ellipse 180px 120px at 52% 58%, var(--sky-light), var(--sky));
  }
  .invite {
    position: absolute; top: 24px; width: 100%; text-align: center;
    color: var(--sun-yellow); font-size: 15px;
  }
  .invite-rule {
    position: absolute; left: 40px; right: 40px; top: 48px;
    height: 1px; background: var(--on-blue);
  }
  .classes-title {
    position: absolute; top: 56px; width: 100%; text-align: center;
    color: var(--sun-yellow); font-weight: 600; font-size: 15px;
  }
  .class-list {
    position: absolute; left: 66px; top: 84px; list-style: none;
    font-size: 15px; line-height: 21px;
  }
  .class-list li { display: flex; }
  .class-name { width: 52px; }
  .free-trial {
    position: absolute; right: 58px; top: 166px;
    color: var(--sun-yellow); font-size: 14px;
  }
  .price {
    position: absolute; left: 98px; top: 206px;
    color: var(--sun-yellow); font-size: 14px;
  }
  .lesson-note {
    position: absolute; left: 150px; top: 234px; font-size: 14px;
  }
</style>
</head>
<body>
  <section class="card card-front">
    <div class="identity">
      <p class="identity-name">Your Name Here</p>
      <p class="identity-role">Position</p>
    </div>
    <div class="divider"></div>
    <ul class="contact-list">
      <li>
        <svg viewBox="0 0 11 11" aria-hidden="true"><rect x="2" y="0.5" width="7" height="10" rx="1.5" fill="none" stroke="#2aa6dd" stroke-width="1.3"/><rect x="3.5" y="2" width="4" height="6" fill="#2aa6dd"/></svg>
        +47 900 xx xxx
      </li>
      <li>
        <svg viewBox="0 0 11 11" aria-hidden="true"><rect x="0.7" y="2" width="9.6" height="7" fill="none" stroke="#2aa6dd" stroke-width="1.2"/><path d="M0.7 2 L5.5 6 L10.3 2" fill="none" stroke="#2aa6dd" stroke-width="1.2"/></svg>
        xxxx@mailnest.com
      </li>
      <li>
        <svg viewBox="0 0 11 11" aria-hidden="true"><circle cx="5.5" cy="5.5" r="4.8" fill="#2aa6dd"/><path d="M0.7 5.5 H10.3 M5.5 0.7 V10.3" stroke="#fff" stroke-width="0.8"/><ellipse cx="5.5" cy="5.5" rx="2" ry="4.8" fill="none" stroke="#fff" stroke-width="0.8"/></svg>
        www.<span class="domain">yourdomain</span>.com
      </li>
      <li>
        <svg viewBox="0 0 11 11" aria-hidden="true"><rect x="0.5" y="0.5" width="10" height="10" rx="1.5" fill="#2aa6dd"/></svg>
        friendpage.com/teaching
      </li>
    </ul>
  </section>

  <section class="card card-back">
    <p class="invite">Feel free at asking me anything about my classes</p>
    <div class="invite-rule"></div>
    <h2 class="classes-title">CLASSES:</h2>
    <ul class="class-list">
      <li>Kids class : ( mum &amp; dad can join) ... 30 minutes / 45 minutes</li>
      <li><span class="class-name">Students</span>&nbsp;:&nbsp; (over age 13) .... 60 minutes / 90 minutes</li>
      <li><span class="class-name">Adult</span>&nbsp;:&nbsp; (over age 19) .... 60 minutes / 90 minutes</li>
    </ul>
    <p class="free-trial">Free trial lesson</p>
    <p class="price">Price: 3150 yen</p>
    <p class="lesson-note">* I'll have both Web Lesson and Face to Face Lesson</p>
  </section>
</body>
</html>
```